SaaS Early tech startup business card design

Unique design for experience ecommerce platform company. the business cards will be used by executive members. conformance with color code is required.

```html
<!DOCTYPE html>
<html lang="en">
<head>
<meta charset="utf-8">
<title>Velmo business card</title>
<link href="https://fonts.googleapis.com/css2?family=Lexend:wght@700&family=Montserrat:wght@400&family=Roboto:wght@400;500&display=swap" rel="stylesheet">
<style>
  :root {
    --backdrop: #6b6868;
    --card: #1f2138;
    --teal: #1fae9a;
    --teal-deep: #1e8f8a;
    --wave-a: rgba(30, 120, 150, 0.28);
    --wave-b: rgba(31, 174, 154, 0.18);
    --white: #f2f3f7;
  }
  * { margin: 0; padding: 0; box-sizing: border-box; }
  html, body { width: 1200px; height: 1200px; overflow: hidden; }
  body { background: var(--backdrop); position: relative; font-family: "Roboto", sans-serif; }

  .card {
    position: absolute;
    width: 595px;
    height: 350px;
    border-radius: 26px;
    background: var(--card);
    overflow: hidden;
  }
  .card--front { left: 298px; top: 198px; }
  .card--back { left: 292px; top: 636px; height: 348px; }

  .front-waves {
    position: absolute;
    inset: 0;
    background:
      radial-gradient(ellipse 70% 40% at 50% 30%, var(--wave-a), transparent 70%),
      radial-gradient(ellipse 40% 45% at 50% 90%, var(--wave-b), transparent 70%);
  }
  .brand-name {
    position: absolute;
    left: 0; right: 0;
    top: 84px;
    text-align: center;
    font-family: "Lexend", sans-serif;
    font-weight: 700;
    font-size: 146px;
    line-height: 1;
    letter-spacing: -2px;
    color: var(--teal);
  }
  .tagline {
    position: absolute;
    left: 0; right: 0;
    top: 244px;
    text-align: center;
    font-family: "Montserrat", sans-serif;
    font-size: 17px;
    letter-spacing: 0.38em;
    color: var(--white);
    padding-left: 0.38em;
  }

  .person {
    position: absolute;
    left: 133px;
    top: 138px;
    width: 160px;
    text-align: center;
  }
  .person__name { font-size: 24px; font-weight: 500; color: var(--teal-deep); line-height: 1.1; letter-spacing: -0.5px; }
  .person__role { font-size: 15px; color: var(--white); margin-top: 3px; }

  .contacts { position: absolute; left: 306px; top: 130px; list-style: none; }
  .contacts li {
    display: flex; align-items: center;
    height: 22px;
    font-size: 15.5px;
    color: var(--white);
  }
  .contacts svg { width: 13px; height: 13px; margin-right: 11px; fill: var(--teal-deep); }

  .address {
    position: absolute;
    left: 0; right: 0;
    top: 237px;
    text-align: center;
    font-size: 15.5px;
    color: var(--white);
  }
  .back-waves {
    position: absolute;
    left: 487px; top: 243px;
    width: 108px; height: 105px;
    background: radial-gradient(circle at 60% 50%, var(--wave-a), transparent 70%);
  }
</style>
</head>
<body>
  <section class="card card--front">
    <div class="front-waves" role="img" aria-label="Faint flowing teal line pattern behind the brand name"></div>
    <div class="brand-name">velmo</div>
    <div class="tagline">SHOP YOUR OWN WAY</div>
  </section>

  <section class="card card--back">
    <div class="person">
      <div class="person__name">Rayan K.</div>
      <div class="person__role">CTO/Owner</div>
    </div>
    <ul class="contacts">
      <li>
        <svg viewBox="0 0 16 16" aria-hidden="true"><path d="M1 5c0-2 3-3 7-3s7 1 7 3v1h-4V5H5v1H1zM3 8h10l1 6H2z"/></svg>
        (00) 4827 VELMO
      </li>
      <li>
        <svg viewBox="0 0 16 16" aria-hidden="true"><path d="M1 3h14v10H1zM2 4l6 5 6-5v1l-6 5-6-5z" fill-rule="evenodd"/></svg>
        info@velmo.net
      </li>
      <li>
        <svg viewBox="0 0 16 16" aria-hidden="true"><circle cx="8" cy="8" r="7"/></svg>
        www.velmo.net
      </li>
    </ul>
    <div class="address">Meridian Tower, Coastline Tech Park, UAE</div>
    <div class="back-waves" role="img" aria-label="Small faint teal line pattern in the corner"></div>
  </section>
</body>
</html>
```